Corporate Design für das Unternehmen Pixel Forge
Zielgruppe
Entwicklung von Web-Apps, Plugins, Middleware. etc.
Zielgruppe sind Webagenturen / Werbeagenturen, die bei umfangreichen Softwarere-Projekten externe Unterstützung benötigen bzw. sich auf den kreativen Teil konzentrireren und den reinen Software-Entwicklungsteil auslagern wollen.
-> d.h. zu ca. 90% B2B
-> kein direkter Kontakt zum Endkunden, Kunden sollte im Normalfall die Agentur sein
Aufgabenstellung
Werte, die die Marke / dase Design vermitteln sollten:
- Qualität / Verlässlichkeit der entwickelten Software-Produkte
- Dennoch Flexibilität / Offenheit für Neues / Dynamik
- Fairness / Integrität den Geschäftspartnern gegenüber
-> Farben eher im bläulichen und/oder grünlichem Bereich
-> evtl. mit einen Akzent in einer freundlicheren Farbe (kein Muss)
"Pixel Forge" kann als zusammenhängendes Wort oder als 2 Wörter geschrieben werden. Ebenfalls ist freigestellt ob die Anfangsbuchstaben als Groß- oder Kleinbuchstaben dargestellt werden.

```html
<!DOCTYPE html>
<html lang="de">
<head>
<meta charset="utf-8">
<title>Pixel Forge – Geschäftsausstattung</title>
<link href="https://fonts.googleapis.com/css2?family=Montserrat:wght@400;500&display=swap" rel="stylesheet">
<style>
  :root {
    --stage: #5f5f5f;
    --teal: #4b929f;
    --teal-soft: #a6c1c9;
    --paper: #ffffff;
    --ink: #3c3c3c;
    --ink-light: #5a5a5a;
    --rule: #bdbdbd;
  }
  * { margin: 0; padding: 0; box-sizing: border-box; }
  html, body { width: 1200px; height: 848px; overflow: hidden; }
  body {
    position: relative;
    background: var(--stage);
    font-family: "Montserrat", sans-serif;
    color: var(--ink);
  }
  .sheet { position: absolute; }

  /* Back of letterhead */
  .sheet--teal { left: 53px; top: 74px; width: 530px; height: 750px; background: var(--teal); }
  .sheet--teal .deco { position: absolute; left: 0; top: 632px; width: 118px; height: 118px; background: var(--teal-soft); }

  /* Letterhead */
  .sheet--letter { left: 381px; top: 34px; width: 530px; height: 750px; background: var(--paper); }
  .brand { position: absolute; display: flex; align-items: center; }
  .brand__dot { background: var(--teal); }
  .brand__name { font-weight: 400; color: var(--ink); letter-spacing: 0.32em; }
  .sheet--letter .brand { left: 36px; top: 52px; gap: 12px; }
  .sheet--letter .brand__dot { width: 26px; height: 26px; }
  .sheet--letter .brand__name { font-size: 15.5px; }

  .address {
    position: absolute; left: 412px; top: 96px;
    border-left: 1px solid var(--teal);
    padding: 0 0 0 6px;
    font-size: 7.4px; line-height: 12.5px; color: var(--ink);
    font-style: normal;
  }
  .foldmark { position: absolute; left: 2px; width: 8px; height: 1px; background: var(--rule); }
  .foldmark--upper { top: 265px; }
  .foldmark--lower { top: 530px; }

  .legal {
    position: absolute; left: 36px; top: 718px;
    font-size: 6.3px; line-height: 9px; color: var(--ink-light);
  }
  .corner-mark { position: absolute; left: 492px; top: 706px; width: 16px; height: 16px; background: var(--teal); }

  /* Business card back */
  .card { width: 214px; height: 138px; }
  .card--back { left: 860px; top: 332px; background: var(--teal); overflow: hidden; }
  .card--back .deco { position: absolute; left: 0; top: 38px; width: 74px; height: 74px; background: var(--teal-soft); }
  .card--back .url {
    position: absolute; left: 100px; top: 65px;
    font-size: 6.4px; letter-spacing: 0.16em; color: var(--paper);
  }

  /* Business card front */
  .card--front { left: 935px; top: 488px; width: 215px; height: 139px; background: var(--paper); }
  .card--front .brand { left: 14px; top: 20px; gap: 8px; }
  .card--front .brand__dot { width: 14px; height: 14px; }
  .card--front .brand__name { font-size: 8.6px; }
  .person { position: absolute; right: 95px; top: 80px; text-align: right; }
  .person__name { font-size: 9.4px; line-height: 11px; color: var(--teal); font-weight: 400; }
  .person__role { font-size: 5.8px; margin-top: 4px; color: var(--ink-light); }
  .card--front .contact {
    position: absolute; left: 129px; top: 81px;
    font-size: 5.9px; line-height: 8.9px; color: var(--ink-light);
    font-style: normal;
  }
</style>
</head>
<body>

  <section class="sheet sheet--teal" aria-label="Briefbogen Rückseite">
    <div class="deco"></div>
  </section>

  <section class="sheet sheet--letter" aria-label="Briefbogen">
    <div class="brand">
      <span class="brand__dot"></span>
      <span class="brand__name">pixelforge</span>
    </div>
    <address class="address">
      musterstraße 12<br>
      12345 musterstadt<br>
      t: +49 (0) 123 45 678<br>
      f: +49 (0)&nbsp; 123 45 678<br>
      info@pixelforge.com<br>
      www.pixelforge.com
    </address>
    <span class="foldmark foldmark--upper"></span>
    <span class="foldmark foldmark--lower"></span>
    <p class="legal">
      Handelsregister Amtsgericht Musterstadt HRA 4127 &nbsp;|&nbsp; Registergericht: Amtsgericht Musterstadt HRB 20871<br>
      UID: DE 987 654 321 &nbsp;|&nbsp; Bankverbindung &nbsp;|&nbsp; IBAN DE 00123456780000000000
    </p>
    <span class="corner-mark"></span>
  </section>

  <section class="sheet card card--back" aria-label="Visitenkarte Rückseite">
    <div class="deco"></div>
    <span class="url">www.pixelforge.com</span>
  </section>

  <section class="sheet card card--front" aria-label="Visitenkarte Vorderseite">
    <div class="brand">
      <span class="brand__dot"></span>
      <span class="brand__name">pixelforge</span>
    </div>
    <div class="person">
      <p class="person__name">maximilian<br>mustermann</p>
      <p class="person__role">geschäftsführer</p>
    </div>
    <address class="contact">
      musterstraße 12<br>
      12345 musterstadt<br>
      t: +49 (0) 123 45 678<br>
      f: +49 (0)&nbsp; 123 45 678<br>
      info@pixelforge.com
    </address>
  </section>

</body>
</html>
```